Fitness Centre/Personal Trainer Business Card

We need a business card design for a company based in Singapore called 'Vigor Ledger'.

We are a team of Personal Trainers and we are planning to open our new training facility.

This design will also be printed/painted on the walls in our gym.

We are a new breed of personal trainers who take fitness seriously and holistically. We do not merely train our clients to be big and muscular.

We believe in wholeness. In our opinion, fitness should include: strength, speed, flexibility, mobility, stamina & agility. These are what we train for. Of course, nutrition/diet is key.

We use fitness tools such as kettlebells, QVL, Pylometric boxes, battling ropes, clubbells, medicine balls, bulgarian bags etc - functional and non-bulky tools.

I currently have a Facebook page 'Vigor Ledger SG' which shows a logo of a kettlebell. But my business focus has since changed.

Services provided:
- Kettlebell Sport Preparation
- Calisthenics Training
- Corrective Exercises
- Sports Strength & Conditioning
- 28 days Weight Loss Program
- Myofascial Rehab Therapy
- Sports/Thai Massage

Main colors for the design should be BLACK & YELLOW. We envision a design which is able to protray the holistic view we take on fitness. Also it should somewhat appeal to the ladies and not intimidate them.

Target Market(s)

People between 18-35 years old. Students and working class alike.

Industry/Entity Type

Training

Requirements
Must have
• Name: Marcus Obadiah Lim
Fitness Coach
Corrective Exercise Specialist
M: +65 9437 2065
E: marcus@sgvigorledger-example.com

Double-sided please.
Nice to have
• "What is your vigor ledger?"

```html
<!DOCTYPE html>
<html lang="en">
<head>
<meta charset="utf-8">
<title>Vigor Ledger – Business Cards</title>
<link href="https://fonts.googleapis.com/css2?family=Source+Sans+3:wght@400;600;700&display=swap" rel="stylesheet">
<style>
  :root{
    --stage:#b9b9b9;
    --ink:#000000;
    --paper:#ffffff;
    --yellow:#f2dc1e;
    --text-dark:#1a1a1a;
    --text-soft:#3a3a3a;
    --divider-dark:#6a6a6a;
    --divider-light:#bdbdbd;
    --ghost:#ece6c4;
  }
  *{margin:0;padding:0;box-sizing:border-box}
  html,body{width:1200px;height:693px;overflow:hidden}
  body{background:var(--stage);font-family:"Source Sans 3",Arial,sans-serif;position:relative}
  .card{position:absolute;width:541px;height:308px;overflow:hidden}
  .card--dark{background:var(--ink);color:var(--paper)}
  .card--light{background:var(--paper);color:var(--text-dark);border:1px solid #8a8a8a}
  .front-dark{left:41px;top:31px}
  .front-light{left:624px;top:31px}
  .back-dark{left:41px;top:358px}
  .back-light{left:624px;top:358px}

  .brand{position:absolute;left:58px;top:120px;width:190px;display:flex;align-items:center;gap:10px}
  .brand__dot{width:22px;height:22px;border-radius:50%;background:var(--yellow);flex:none}
  .brand__name{font-size:27px;font-weight:700;line-height:1;white-space:nowrap;color:var(--yellow)}
  .card--light .brand__name{color:var(--text-dark)}

  .divider{position:absolute;left:252px;top:38px;width:1px;height:218px;background:var(--divider-dark)}
  .card--light .divider{background:var(--divider-light)}

  .person{position:absolute;left:278px;top:78px}
  .person__name{font-size:20px;font-weight:700;line-height:1.2;color:var(--yellow)}
  .card--light .person__name{color:var(--text-dark)}
  .person__role{font-size:15px;line-height:19px}
  .contacts{list-style:none;margin-top:23px}
  .contacts li{font-size:15px;line-height:25px;display:flex;align-items:center;gap:5px}
  .card--light .contacts li{color:var(--text-soft)}
  .contacts svg{width:11px;height:11px;fill:var(--yellow)}
  .card--light .contacts svg{fill:var(--text-soft)}

  .services-title{font-size:19px;font-weight:700}
  .back-dark .services-title{position:absolute;left:278px;top:28px}
  .services{list-style:none}
  .back-dark .services{position:absolute;left:278px;top:68px}
  .back-dark .services li{font-size:15.5px;line-height:26.5px;letter-spacing:.2px}
  .services li::before{content:"•";margin-right:3px}
  .motto{font-weight:700;letter-spacing:1px}
  .back-dark .motto{position:absolute;left:140px;top:270px;font-size:16px;color:var(--yellow)}

  .ghost-name{position:absolute;left:0;right:0;top:122px;text-align:center;font-size:58px;font-weight:700;color:var(--ghost)}
  .back-light .services-title{position:absolute;left:0;right:0;top:72px;text-align:center}
  .services-grid{position:absolute;left:0;right:0;top:118px;text-align:center;list-style:none}
  .services-grid .row{font-size:17px;line-height:34px}
  .services-grid span{margin:0 2px}
  .services-grid span::before{content:"•";margin-right:3px}
  .back-light .motto{position:absolute;left:0;right:0;top:274px;text-align:center;font-size:16px;letter-spacing:.2px;color:var(--ink)}
</style>
</head>
<body>

<svg width="0" height="0" style="position:absolute" aria-hidden="true">
  <symbol id="icon-phone" viewBox="0 0 12 12"><path d="M3 0h6v12H3zM4 1.5v6h4v-6zM5 9h2v1.5H5z"/></symbol>
  <symbol id="icon-mail" viewBox="0 0 12 12"><path d="M0 3h12v7H0zM1 4l5 3.5L11 4v-.2L6 6.6 1 3.8z"/></symbol>
  <symbol id="icon-web" viewBox="0 0 12 12"><path d="M6 0a6 6 0 1 0 0 12A6 6 0 0 0 6 0zm0 1.2c.8 1 1.3 2.4 1.4 4.2H4.6C4.7 3.6 5.2 2.2 6 1.2zM1.3 5.4a4.8 4.8 0 0 1 2.5-3.6 8 8 0 0 0-.8 3.6zm0 1.2H3a8 8 0 0 0 .8 3.6 4.8 4.8 0 0 1-2.5-3.6zm3.3 0h2.8c-.1 1.8-.6 3.2-1.4 4.2-.8-1-1.3-2.4-1.4-4.2zm4.4 0h1.7a4.8 4.8 0 0 1-2.5 3.6 8 8 0 0 0 .8-3.6zm0-1.2a8 8 0 0 0-.8-3.6 4.8 4.8 0 0 1 2.5 3.6z"/></symbol>
</svg>

<section class="card card--dark front-dark">
  <div class="brand"><span class="brand__dot"></span><span class="brand__name">Vigor Ledger</span></div>
  <div class="divider"></div>
  <div class="person">
    <h1 class="person__name">Marcus Obadiah Lim</h1>
    <p class="person__role">Fitness Coach</p>
    <p class="person__role">Corrective Exercise Specialist</p>
    <ul class="contacts">
      <li><svg><use href="#icon-phone"/></svg>+65 9437 2065</li>
      <li><svg><use href="#icon-mail"/></svg>marcus@sgvigorledger-example.com</li>
      <li><svg><use href="#icon-web"/></svg>www.sgvigor-example.com</li>
    </ul>
  </div>
</section>

<section class="card card--light front-light">
  <div class="brand"><span class="brand__dot"></span><span class="brand__name">Vigor Ledger</span></div>
  <div class="divider"></div>
  <div class="person">
    <h1 class="person__name">Marcus Obadiah Lim</h1>
    <p class="person__role">Fitness Coach</p>
    <p class="person__role">Corrective Exercise Specialist</p>
    <ul class="contacts">
      <li><svg><use href="#icon-phone"/></svg>+65 9437 2065</li>
      <li><svg><use href="#icon-mail"/></svg>marcus@sgvigorledger-example.com</li>
      <li><svg><use href="#icon-web"/></svg>www.sgvigor-example.com</li>
    </ul>
  </div>
</section>

<section class="card card--dark back-dark">
  <div class="brand"><span class="brand__dot"></span><span class="brand__name">Vigor Ledger</span></div>
  <h2 class="services-title">Services</h2>
  <ul class="services">
    <li>Sports Strength &amp; Conditioning</li>
    <li>Kettlebell Sport Preparation</li>
    <li>28 days Weight Loss Program</li>
    <li>Myofascial Rehab Therapy</li>
    <li>Calisthenics Training</li>
    <li>Corrective Exercises</li>
    <li>Sports/Thai Massage</li>
  </ul>
  <p class="motto">What is your vigor ledger ?</p>
</section>

<section class="card card--light back-light">
  <p class="ghost-name" aria-hidden="true">Vigor Ledger</p>
  <h2 class="services-title">Services</h2>
  <div class="services-grid">
    <p class="row"><span>Sports Strength &amp; Conditioning</span><span>Sports/Thai Massage</span></p>
    <p class="row"><span>Kettlebell Sport Preparation</span><span>Corrective Exercises</span></p>
    <p class="row"><span>28 days Weight Loss Program</span><span>Calisthenics Training</span></p>
    <p class="row"><span>Myofascial Rehab Therapy</span></p>
  </div>
  <p class="motto">What is your vigor ledger ?</p>
</section>

</body>
</html>
```